Sunset Harbor Living Web Page

We need a web page design that has two intro pages - first being a 'home page', then a link to the second page that has the 'content tabs' and a 'call to action' (see below).

The business helps people that wish to retire to S.E.Asia (Thailand, Malaysia, Indonesia,The Philippines etc) - to enjoy the lifestyle and the remaining years of their lives. What attracts S.E.Asia to many people is the lower cost, the atmoshpere and beauty of the tropics and the vibrancy of the various countries.

People that are wishing to make the most of their retirement and are adventurous at a great bargain compared to the cost of their own countries will be interested.

We help them achieve this - visa, financials (tax, gov't payments etc), introduce them to the right people for property, clubs, retirement facilities, insurance and so forth.

Therefore we are providing an extremely wide ranging service and this site will provide broad but general information only - with a call to action to come and see us for more specific information and how we can help them specifically.

This site will be predominantly for travel and lifestyle, it will be linked with another financial services (financial planning) site later down the track.

The colour scheme is dark green and blue - as per the attached logo design. Photos and background just think lifestyle and S.E.Asia - beaches/mountains/water/recreational activities for retirees.

Target market is mostly those coming up to retirement to those that are already retired. But we also expect to have some interest with younger people that would like to find out more and plan for the future. So a broad age group but I would say mostly 40-70 yrs old.

On the first (Home) page we would like our company name 'Sunset Harbor Living', our logo (which will be on all pages) and a statement such as: “Imagine a retirement where your dreams are brought to life, and you have never felt more alive. Let us show you how”. Then a link to the second page.

We would like an uncluttered site. On the second (contents) page the tabs would be:

- Visa
- Property
- Financials
- Travel
- Insurance & Healthcare
- Medical Tourism
- Cost of living
- Weekly Blogs and articles
- Sunset Harbor Living story

We would also like a call to action on the second page - asking them to leave their contact details if they wish to learn more or sign up to our weekly newsletter/blog.

We are open to suggestions and your imaginations.

Thank you
Malcolm

Font styles to use
Serif
Script

Colors
0255a3
3377b5
00a990
9bcb3c
abd036
33b8a4
85abd2
cadf82
86cfc6

Requirements
Must have
• I have been asked by the web designer to receive a 'Web Font' so that we can 'get off of Zentrofy'. Hope that makes sense.

```html
<!DOCTYPE html>
<html lang="en">
<head>
<meta charset="utf-8">
<title>Sunset Harbor Living</title>
<link href="https://fonts.googleapis.com/css2?family=Raleway:wght@500;600;700&family=Open+Sans:ital,wght@0,400;0,600;1,400&family=Oswald:wght@500&display=swap" rel="stylesheet">
<style>
:root{
  --green:#8cc63f;
  --green-dark:#6aa52a;
  --blue:#0b7dcb;
  --blue-band:#3a7ec2;
  --blue-deep:#1f5fa8;
  --ink:#222;
  --muted:#666;
  --line:#e2e2e2;
  --grey-bg:#f1f1f1;
  --white:#fff;
}
*{box-sizing:border-box;margin:0;padding:0}
html,body{width:685px;height:1200px;overflow:hidden;background:var(--white)}
body{position:relative;font-family:"Open Sans",sans-serif;color:var(--ink)}
section,header,footer{position:absolute;left:0;width:685px}
h2{font-family:"Raleway",sans-serif;font-weight:700;font-size:13px;letter-spacing:.2px;color:var(--ink);text-transform:uppercase}
.more{font-family:"Raleway",sans-serif;font-size:7px;font-weight:700;color:var(--green);text-decoration:none;text-transform:uppercase}

/* header */
.site-header{top:0;height:52px;border-top:2px solid var(--green);background:var(--white);z-index:3}
.brand{position:absolute;left:50px;top:2px;width:86px;height:78px;border-radius:0 0 43px 43px;background:var(--white);box-shadow:0 3px 6px rgba(0,0,0,.2);display:flex;align-items:center;justify-content:center;gap:3px;flex-direction:column}
.brand-dot{width:18px;height:18px;border-radius:50%;background:var(--green)}
.brand-name{font-family:"Raleway",sans-serif;font-weight:700;font-size:8.5px;color:var(--blue);text-align:center;line-height:1.1}
.search{position:absolute;left:430px;top:8px;width:130px;height:18px;border:1px solid var(--line);font-size:7px;color:#888;padding:4px 6px}
.search svg{position:absolute;right:5px;top:4px}
.signin{position:absolute;left:572px;top:11px;font-size:7px;color:var(--green);display:flex;gap:5px;align-items:center}
.main-nav{position:absolute;left:149px;top:35px;display:flex;gap:7.6px;font-size:7px;font-weight:600}
.main-nav a{color:var(--ink);text-decoration:none}
.main-nav a.current{color:var(--green)}

/* hero */
.hero{top:52px;height:248px;background:linear-gradient(180deg,#9fc9d8 0%,#6f9a7a 38%,#3d7d6a 55%,#4fb3b0 72%,#8fd0c8 100%)}
.hero h1{position:absolute;top:62px;width:100%;text-align:center;font-family:"Raleway",sans-serif;font-weight:500;font-size:19.5px;line-height:26px;color:var(--white);text-shadow:0 1px 3px rgba(0,0,0,.5)}
.hero .cta{position:absolute;left:275px;top:149px;width:135px;height:28px;border:2px solid var(--white);background:var(--green);color:var(--white);font-family:"Raleway",sans-serif;font-weight:700;font-size:8px;letter-spacing:.3px;display:flex;align-items:center;justify-content:center}
.dots{position:absolute;top:222px;left:296px;display:flex;gap:4px}
.dots i{width:20px;height:4px;border-radius:2px;background:var(--white)}
.dots i.on{background:var(--green)}

/* newsletter */
.newsletter{top:300px;height:48px;background:var(--blue-band);color:var(--white)}
.newsletter svg{position:absolute;left:56px;top:10px}
.newsletter .label{position:absolute;left:102px;top:12px;font-family:"Raleway",sans-serif;font-weight:600;font-size:8.5px;line-height:12px}
.newsletter .label b{display:block;font-size:11px;font-weight:700}
.newsletter .field{position:absolute;left:269px;top:12px;width:295px;height:25px;background:var(--white);font-size:7px;color:#888;padding:8px 12px}
.newsletter .go{position:absolute;left:564px;top:12px;width:65px;height:25px;background:var(--green);font-family:"Raleway",sans-serif;font-weight:700;font-size:8px;display:flex;align-items:center;justify-content:center}

/* intro */
.intro{top:348px;height:200px}
.intro h2{position:absolute;left:56px;top:24px}
.intro .copy{position:absolute;left:56px;top:46px;width:295px;font-size:6.6px;line-height:13.5px;color:var(--muted)}
.intro .copy p{margin-bottom:13px}
.intro .frame{position:absolute;left:384px;top:23px;width:245px;height:151px;border:1px solid var(--line);padding:3px;background:var(--white)}
.ph{width:100%;height:100%}
.ph-couple{background:linear-gradient(90deg,#1e8fb8,#3aa8cc 55%,#dfe9ef)}

/* places */
.places{top:548px;height:240px;background:var(--grey-bg)}
.places h2{position:absolute;top:22px;width:100%;text-align:center}
.card{position:absolute;top:50px;width:135px;height:164px;background:var(--white);border:1px solid var(--line);padding:3px}
.card .img{height:78px}
.card h3{font-family:"Raleway",sans-serif;font-weight:600;font-size:8.5px;margin:7px 0 2px 4px}
.stars{margin-left:4px;color:var(--green);font-size:7px;letter-spacing:.5px}
.card p{margin:4px 4px 0;font-size:6px;line-height:12.5px;color:var(--muted)}
.card .plus{position:absolute;right:2px;bottom:2px}

/* columns */
.columns{top:788px;height:246px}
.col{position:absolute;top:24px}
.cats{left:56px;width:160px}
.cats ul{list-style:none;margin-top:17px}
.cats li{font-size:6.5px;color:#555;height:30.5px;display:flex;gap:7px}
.cats li::before{content:"";width:8px;height:8px;border-radius:50%;background:var(--green);flex:none}
.mag{left:232px;width:178px}
.mag .cover{margin-top:15px;width:178px;height:166px;border:1px solid var(--line);padding:3px}
.mag .cover div{height:100%;background:linear-gradient(135deg,#1f5fa8,#4a93cf 60%,#b9d6ea);padding:14px 12px;color:var(--white)}
.mag .cover b{font-family:"Oswald",sans-serif;font-weight:500;font-size:14px;display:block;margin-bottom:5px}
.mag .cover i{font-size:7px;line-height:13.5px;display:block;width:110px}
.blogs{left:432px;width:200px}
.post{display:flex;gap:9px;margin-top:14px;height:40px}
.post:first-of-type{margin-top:17px}
.post .thumb{width:60px;height:43px;flex:none;border:1px solid var(--line);padding:2px}
.post .thumb div{height:100%;background:linear-gradient(180deg,#7fb6d8,#2f8fc2)}
.post h4{font-family:"Raleway",sans-serif;font-weight:600;font-size:6.5px;line-height:11.5px;color:#333;max-width:124px}
.post .meta{font-size:6px;color:var(--green);margin-top:2px}
.columns .more{position:absolute;top:211px}

/* footer */
.site-footer{top:1034px;height:166px;background:var(--blue);color:var(--white)}
.f-brand{position:absolute;left:56px;top:28px;width:100px;display:flex;flex-direction:column;align-items:center;gap:6px}
.f-brand .dot{width:34px;height:34px;border-radius:50%;background:var(--white)}
.f-brand span{font-family:"Raleway",sans-serif;font-weight:700;font-size:11px;text-align:center;line-height:1.15}
.f-col{position:absolute;top:20px}
.f-col h5{font-family:"Raleway",sans-serif;font-weight:600;font-size:8.5px;margin-bottom:7px}
.f-col a{display:block;font-size:6.5px;line-height:13.3px;color:#d8e9f6;text-decoration:none}
.bottom{position:absolute;left:0;top:126px;width:685px;height:40px;background:var(--blue-deep)}
.bottom p{position:absolute;left:56px;top:15px;font-size:6.5px}
.social{position:absolute;right:56px;top:10px;display:flex;gap:4px}
.social i{width:19px;height:19px;border:1.5px solid var(--white);border-radius:50%}
</style>
</head>
<body>

<header class="site-header">
  <div class="brand"><span class="brand-dot"></span><span class="brand-name">Sunset Harbor<br>Living</span></div>
  <div class="search">Search
    <svg width="8" height="8" viewBox="0 0 10 10"><circle cx="4" cy="4" r="3" fill="none" stroke="#aaa" stroke-width="1.2"/><path d="M6.3 6.3 9 9" stroke="#aaa" stroke-width="1.2"/></svg>
  </div>
  <div class="signin">
    <svg width="7" height="9" viewBox="0 0 7 9"><rect y="3.5" width="7" height="5.5" fill="#8cc63f"/><path d="M1.5 4V2.5a2 2 0 0 1 4 0V4" fill="none" stroke="#8cc63f" stroke-width="1.2"/></svg>
    User Sign in
  </div>
  <nav class="main-nav">
    <a class="current" href="#">Home</a><a href="#">Visa</a><a href="#">Property</a><a href="#">Financials</a><a href="#">Travel</a><a href="#">Insurance &amp; Healthcare</a><a href="#">Medical Tourism</a><a href="#">Cost of living</a><a href="#">Blogs &amp; articles</a><a href="#">Story</a><a href="#">Contact</a>
  </nav>
</header>

<section class="hero" role="img" aria-label="Tropical bay with limestone cliffs and long-tail boats on turquoise water">
  <h1>Imagine a retirement where your dreams<br>are brought to life, and you have never felt more<br>alive. Let us show you how</h1>
  <a class="cta">GET MORE INFORMATION</a>
  <div class="dots"><i class="on"></i><i></i><i></i><i></i></div>
</section>

<section class="newsletter">
  <svg width="36" height="30" viewBox="0 0 36 30"><g transform="rotate(-14 18 15)"><rect x="3" y="6" width="30" height="20" rx="2" fill="#fff"/><path d="M3 7 18 18 33 7" fill="none" stroke="#3a7ec2" stroke-width="2"/></g></svg>
  <div class="label">SIGN UP TO OUR<b>WEEKLY NEWSLETTER</b></div>
  <div class="field">EMAIL ADDRESS</div>
  <div class="go">SIGN IN</div>
</section>

<section class="intro">
  <h2>Sunset Harbor Living</h2>
  <div class="copy">
    <p>At vero eos et accusamus et iusto odio dignissimos ducimus qui blanditiis praesentium vol uptatum deleniti atque corrupti quos dolores et quas molestias excepturi sint occaecati cu piditate non provident, similique sunt in culpa qui officia deserunt mollitia animi, id est lab orum et dolorumerum facilis est et expedita distinctio.</p>
    <p>Nam libero tempore, cum soluta nobis est eligendi optio cumque nihil impedit quo minus id quod max ime placeat facere punt in culpa qui officia deseossimus, omnis voluptas assume nda est, omnis dolor repell endus.</p>
    <a class="more" href="#">Read more &gt;&gt;</a>
  </div>
  <div class="frame"><div class="ph ph-couple" role="img" aria-label="Retired couple relaxing on a boat deck over blue sea"></div></div>
</section>

<section class="places">
  <h2>Best places to live</h2>
  <article class="card" style="left:56px"><div class="img" role="img" aria-label="Thai beach with limestone cliffs and boats" style="background:linear-gradient(180deg,#bfe0ef,#4c8f4f 50%,#5fd0cc)"></div><h3>Thailand</h3><div class="stars">★★★★★</div><p>Nam libero tempore, cum soluta nobi est eligendi optio cumque nihil imped it quo minus id quod maxi..</p><svg class="plus" width="20" height="20" viewBox="0 0 20 20"><path d="M20 0V20H0Z" fill="#8cc63f"/><path d="M14 10v6M11 13h6" stroke="#fff" stroke-width="1.5"/></svg></article>
  <article class="card" style="left:201px"><div class="img" role="img" aria-label="Aerial view of a Malaysian lagoon" style="background:linear-gradient(180deg,#a9cde6,#1b6aa8 50%,#3bc1b5)"></div><h3>Malaysia</h3><div class="stars">★★★★★</div><p>Nam libero tempore, cum soluta nobi est eligendi optio cumque nihil imped it quo minus id quod maxi..</p><svg class="plus" width="20" height="20" viewBox="0 0 20 20"><path d="M20 0V20H0Z" fill="#8cc63f"/><path d="M14 10v6M11 13h6" stroke="#fff" stroke-width="1.5"/></svg></article>
  <article class="card" style="left:347px"><div class="img" role="img" aria-label="Indonesian volcano crater lake" style="background:linear-gradient(180deg,#2f5f9c,#6a6a52 50%,#2f6b55)"></div><h3>Indonesia</h3><div class="stars">★★★★★</div><p>Nam libero tempore, cum soluta nobi est eligendi optio cumque nihil imped it quo minus id quod maxi..</p><svg class="plus" width="20" height="20" viewBox="0 0 20 20"><path d="M20 0V20H0Z" fill="#8cc63f"/><path d="M14 10v6M11 13h6" stroke="#fff" stroke-width="1.5"/></svg></article>
  <article class="card" style="left:492px"><div class="img" role="img" aria-label="Island cove in the Philippines" style="background:linear-gradient(180deg,#cfe3ee,#3f7a3c 50%,#49c3c0)"></div><h3>The Philippines</h3><div class="stars">★★★★★</div><p>Nam libero tempore, cum soluta nobi est eligendi optio cumque nihil imped it quo minus id quod maxi..</p><svg class="plus" width="20" height="20" viewBox="0 0 20 20"><path d="M20 0V20H0Z" fill="#8cc63f"/><path d="M14 10v6M11 13h6" stroke="#fff" stroke-width="1.5"/></svg></article>
</section>

<section class="columns">
  <div class="col cats">
    <h2>Popular categories</h2>
    <ul>
      <li>Blanditiis praesentiudignissimos ducimus</li>
      <li>Officia deserunt mollitia animipossimusdr</li>
      <li>Temporibus autem quibufertusdam et aut</li>
      <li>At vero eos et accusamus et iusto odiodert</li>
      <li>Et harum quidem rerum facigsertlis est et</li>
    </ul>
  </div>
  <div class="col mag">
    <h2>Out magazine</h2>
    <div class="cover"><div role="img" aria-label="Magazine cover with a retired couple on a sailing boat"><b>SUNSET HARBOR</b><i>Nor again is there anyone who loves or pursues or desires to obtain pain of itself, because it is pain, but because occasionally circumstances occur in which toil and pain can procure him some great pleasure.</i></div></div>
  </div>
  <div class="col blogs">
    <h2>Weekly blogs &amp; articles</h2>
    <div class="post"><div class="thumb"><div role="img" aria-label="Couple kayaking"></div></div><div><h4>AT VERO EOS ET ACCUSAMUS ETIUS TO ODIO DIGNISSIMOS</h4><div class="meta">▦ 04/04/2016 &nbsp;| &nbsp;● John Doe</div></div></div>
    <div class="post"><div class="thumb"><div role="img" aria-label="Beach and sea"></div></div><div><h4>AT VERO EOS ET ACCUSAMUS ETIUS TO ODIO DIGNISSIMOS</h4><div class="meta">▦ 04/04/2016 &nbsp;| &nbsp;● John Doe</div></div></div>
    <div class="post"><div class="thumb"><div role="img" aria-label="Couple at a harbour"></div></div><div><h4>AT VERO EOS ET ACCUSAMUS ETIUS TO ODIO DIGNISSIMOS</h4><div class="meta">▦ 04/04/2016 &nbsp;| &nbsp;● John Doe</div></div></div>
  </div>
  <a class="more" href="#" style="left:57px">Read more &gt;&gt;</a>
  <a class="more" href="#" style="left:433px">View more &gt;&gt;</a>
</section>

<footer class="site-footer">
  <div class="f-brand"><span class="dot"></span><span>Sunset Harbor<br>Living</span></div>
  <div class="f-col" style="left:183px"><h5>About us</h5><a>Our Story</a><a>Team</a><a>Newsletters</a><a>Contact</a><a>Jobs</a><a>Help Us Grow</a></div>
  <div class="f-col" style="left:264px"><h5>Quick Links</h5><a>Tour info</a><a>Packages</a><a>Route Planner Info</a><a>About us</a><a>Contact us</a></div>
  <div class="f-col" style="left:357px"><h5>Info &amp; Help</h5><a>FAQs</a><a>Contact Us</a><a>Lost Property</a><a>Terms and Conditions</a><a>Privacy Policy</a></div>
  <div class="f-col" style="left:467px"><h5>Resources</h5><a>Roadmap &amp; Updates</a><a>Security</a><a>Privacy Policy</a><a>Terms of Service</a><a>Webinars</a><a>Free for Startups</a></div>
  <div class="f-col" style="left:572px"><h5>Legal</h5><a>Certified Trainers</a><a>Teamwork</a><a>Developer Zone</a><a>Referral Program</a><a>Refund Policy</a><a>Login</a></div>
  <div class="bottom">
    <p>Copyright © 2016 , Sunset Harbor Living. All rights reserved.</p>
    <div class="social"><i></i><i></i><i></i><i></i></div>
  </div>
</footer>

</body>
</html>
```